Brookvane Consulting Business Card Design

Business Card Design for Brookvane Consulting. Brookvane Consulting is a boutique consultancy based in Atlanta, GA., that specializes in marketing strategy, organization planning, and leadership development. We provide solutions for small businesses and startups as well as Vantage 300 companies.

http://brookvaneconsulting.com/

Target Market(s)

We provide solutions for small businesses and startups as well as Vantage 300 companies.

Industry/Entity Type

Consulting

Contact Information for Business Card

Two sided business card with priority on contact information, logo, tag line (Inspiration to Dream More, Do More, Become More)

Colors

Designer to choose colors to be used in the design.

Requirements
Must have
• contact information, logo, tag line (Inspiration to Dream More, Do More, Become More)
• Simple no over communication.
Nice to have
• I would like to see different placements of logo and creative use of both sides of the card
Should not have
• Do not put too much information on the card.

```html
<!DOCTYPE html>
<html lang="en">
<head>
<meta charset="UTF-8">
<title>Brookvane Consulting – Business Card</title>
<link href="https://fonts.googleapis.com/css2?family=Work+Sans:wght@400;500;600&family=Exo+2:wght@500&display=swap" rel="stylesheet">
<style>
  :root {
    --bg: #1c1c1c;
    --card: #262626;
    --card-edge: #2e2e2e;
    --ink: #f2f2f2;
    --ink-soft: #d8d8d8;
    --ink-muted: #a8a8a8;
    --emboss: #8c8c8c;
  }
  * { margin: 0; padding: 0; box-sizing: border-box; }
  html, body { width: 1200px; height: 900px; overflow: hidden; }
  body {
    background: var(--bg);
    font-family: "Work Sans", sans-serif;
    color: var(--ink);
    position: relative;
  }
  .card {
    position: absolute;
    left: 250px;
    width: 700px;
    height: 400px;
    background: var(--card);
    border: 1px solid var(--card-edge);
    box-shadow: 0 18px 40px rgba(0,0,0,.55);
  }
  .card--front { top: 35px; }
  .card--back { top: 465px; }

  /* front */
  .front__brand {
    position: absolute;
    top: 105px; left: 0; right: 0;
    text-align: center;
    line-height: 1.05;
    color: var(--emboss);
    font-weight: 600;
  }
  .front__brand-main { display: block; font-size: 76px; letter-spacing: 1px; }
  .front__brand-sub { display: block; font-size: 30px; letter-spacing: 7px; text-transform: uppercase; }
  .front__tagline {
    position: absolute;
    top: 252px; left: 0; right: 0;
    text-align: center;
    font-size: 15px;
    letter-spacing: 1.5px;
    color: var(--ink-muted);
  }
  .front__web {
    position: absolute;
    bottom: 58px; left: 0; right: 0;
    text-align: center;
    font-size: 19px;
    letter-spacing: 3px;
    color: var(--ink);
  }

  /* back */
  .back__brand {
    position: absolute;
    left: 45px; top: 135px;
    width: 285px;
    color: var(--ink);
    font-weight: 600;
    line-height: 1.05;
  }
  .back__brand-main { display: block; font-size: 52px; }
  .back__brand-sub { display: block; font-size: 21px; letter-spacing: 6px; text-transform: uppercase; }
  .back__divider {
    position: absolute;
    left: 345px; top: 60px;
    width: 2px; height: 240px;
    background: var(--ink);
  }
  .back__details { position: absolute; left: 385px; top: 62px; width: 300px; }
  .back__name {
    font-family: "Exo 2", sans-serif;
    font-weight: 500;
    font-size: 25px;
    letter-spacing: 2px;
    text-transform: uppercase;
  }
  .back__title { font-size: 17px; color: var(--ink-soft); margin-top: 2px; letter-spacing: .5px; }
  .back__address { font-size: 16px; line-height: 1.35; margin-top: 26px; color: var(--ink-soft); }
  .back__contacts { list-style: none; margin-top: 22px; }
  .back__contacts li {
    display: flex; align-items: center; gap: 12px;
    font-size: 16px; line-height: 1.6; letter-spacing: .3px;
  }
  .back__contacts svg { width: 14px; height: 14px; flex: none; fill: var(--ink); }
</style>
</head>
<body>
  <section class="card card--front">
    <div class="front__brand">
      <span class="front__brand-main">Brookvane</span>
      <span class="front__brand-sub">Consulting</span>
    </div>
    <p class="front__tagline">Inspiration to Dream More, Do More, Become More</p>
    <p class="front__web">www.brookvaneconsulting.com</p>
  </section>

  <section class="card card--back">
    <div class="back__brand">
      <span class="back__brand-main">Brookvane</span>
      <span class="back__brand-sub">Consulting</span>
    </div>
    <div class="back__divider"></div>
    <div class="back__details">
      <h1 class="back__name">Daniel Hartwell</h1>
      <p class="back__title">Managing Director</p>
      <p class="back__address">418 Marlow Avenue,<br>Suite 12/B, Atlanta</p>
      <ul class="back__contacts">
        <li>
          <svg viewBox="0 0 24 24" aria-hidden="true"><path d="M6.6 10.8a15.1 15.1 0 0 0 6.6 6.6l2.2-2.2a1 1 0 0 1 1-.25 11.4 11.4 0 0 0 3.6.57 1 1 0 0 1 1 1V20a1 1 0 0 1-1 1A17 17 0 0 1 3 4a1 1 0 0 1 1-1h3.5a1 1 0 0 1 1 1c0 1.25.2 2.45.57 3.57a1 1 0 0 1-.25 1z"/></svg>
          404-555-0186
        </li>
        <li>
          <svg viewBox="0 0 24 24" aria-hidden="true"><path d="M2 5h20v14H2z M4 7v.5l8 5 8-5V7l-8 5z" fill-rule="evenodd"/></svg>
          daniel@brookvaneconsulting.com
        </li>
        <li>
          <svg viewBox="0 0 24 24" aria-hidden="true"><path fill="none" stroke="#f2f2f2" stroke-width="2" d="M12 2a10 10 0 1 0 0 20 10 10 0 0 0 0-20zM2 12h20M12 2c3 3 3 17 0 20M12 2c-3 3-3 17 0 20"/></svg>
          www.brookvaneconsulting.com
        </li>
      </ul>
    </div>
  </section>
</body>
</html>
```